Revamp Of Landing Page For an Automated AI Voice Agents Agency

here is my current landing page https://app.brightfernpromotionhub.biz/v2/preview/WXKRPmQ4hLzYBvNdTeGS?notrack=true

Please use all my current content and imagery of ai agents in your new design. Make it easy to ready, easy to navigate and easy to understand

I am looking for a SLEEK shiny polished looking website. I like Dark themed sites but am open to see light themed sites too so please dont be shy.

The site should have an Ai Voice Agent Theme about it. Maybe look and feel of futureistic but simple and not intimidating to the average person...

Here are a couple website designs I like for reference:
https://q7v.io/
https://ai-bots.marekholvin.com/
https://chatwelmo.com/ai-agents

Target Market(s)

b2b

Industry/Entity Type

AI Voice Agents

Coding

Coded - Design and coding required

Font styles to use
Other font styles liked:
• open

Requirements
Must have
• all elements and content and images used in existing design.
Nice to have
• open
Should not have
• open

```html
<!DOCTYPE html>
<html lang="en">
<head>
<meta charset="UTF-8">
<title>Halvora — AI Voice Agents</title>
<link rel="stylesheet" href="https://fonts.googleapis.com/css2?family=DM+Serif+Display&family=Poppins:wght@400;500;600;700&display=swap">
<style>
:root{
  --bg:#05070d;
  --navy:#0b0f1d;
  --panel:#0e121b;
  --violet:#5b2bd9;
  --violet-2:#7b3cf0;
  --indigo:#2a1480;
  --lilac:#a98cf2;
  --lavender:#e9ddfb;
  --orange:#f28a3a;
  --white:#ffffff;
  --muted:#d4d6de;
  --serif:"DM Serif Display", Georgia, serif;
  --sans:"Poppins", Arial, sans-serif;
}
*{margin:0;padding:0;box-sizing:border-box}
html,body{width:1200px;height:5343px;overflow:hidden}
body{background:var(--bg);color:var(--white);font-family:var(--sans);position:relative}
section,footer{position:absolute;left:0;width:1200px;overflow:hidden}
.abs{position:absolute}
.center{left:0;width:1200px;text-align:center}
.serif-title{font-family:var(--serif);text-transform:uppercase;font-weight:400;letter-spacing:-.5px;line-height:1.12}
.copy{font-size:13px;line-height:23px;color:var(--muted)}
.btn{position:absolute;left:459px;width:282px;height:50px;border-radius:25px;background:linear-gradient(90deg,#4a2bd6,#7a3bf2);color:#fff;font-size:12px;font-weight:600;display:flex;align-items:center;justify-content:center;gap:8px;letter-spacing:.3px;border:2px solid rgba(255,255,255,.25)}
.btn.ghost{background:transparent;border:2px solid rgba(255,255,255,.7)}
.btn svg{width:13px;height:13px}
.brand{font-family:var(--sans);font-weight:600;font-size:38px;letter-spacing:0;text-align:center;line-height:46px}

/* hero */
.hero{top:0;height:870px;background:radial-gradient(ellipse at 60% 35%,#1b1540 0%,#0a0d1c 55%,#05070d 100%)}
.hero .brand{position:absolute;top:36px;left:0;width:1200px}
.hero h1{top:130px;font-size:52px;color:var(--lilac)}
.hero-visual{left:484px;top:289px;width:232px;height:232px;border-radius:50%;background:radial-gradient(circle,#2f48c9 0%,#5d2bb8 45%,#a0307a 70%,rgba(10,13,28,0) 72%)}
.feature{position:absolute;width:200px;text-align:center;font-size:13px;font-weight:500}
.feature .ico{width:46px;height:46px;border-radius:50%;background:#fff;margin:0 auto 10px;display:flex;align-items:center;justify-content:center}
.feature .ico svg{width:24px;height:24px;stroke:#1b1540;fill:none;stroke-width:1.8}
.hero h2{top:612px;font-size:27px;font-weight:600}
.hero .copy{top:662px;left:250px;width:700px;text-align:center}

/* workforce */
.workforce{top:870px;height:940px;background:radial-gradient(ellipse at 50% 35%,#16204a 0%,#070a14 60%)}
.workforce h2{top:56px;font-size:46px}
.agent{position:absolute;border-radius:12px;border:3px solid #fff;overflow:hidden}
.agent .ph{width:100%;height:100%}
.agent-label{position:absolute;font-size:12px;font-weight:700;text-align:center;width:240px}
.arrow{position:absolute;width:52px;height:52px;border-radius:50%;background:#fff;display:flex;align-items:center;justify-content:center}
.arrow svg{width:18px;height:18px;stroke:#1b1540;fill:none;stroke-width:2.4}
.badge{left:566px;top:480px;width:70px;height:70px;border-radius:50%;background:linear-gradient(135deg,#4a2bd6,#7a3bf2);border:3px solid #fff;display:flex;align-items:center;justify-content:center}
.badge svg{width:34px;height:34px;stroke:#fff;fill:none;stroke-width:1.8}
.workforce h3{top:576px;font-size:20px;font-weight:600}
.workforce .agent-copy{top:618px;left:380px;width:440px;text-align:center;font-size:12px;line-height:21px}
.workforce .foot-copy{top:802px;left:220px;width:760px;text-align:center}

/* wish */
.wish{top:1810px;height:526px;background:var(--panel)}
.wish-visual{left:0;top:20px;width:600px;height:480px;background:radial-gradient(ellipse at 45% 40%,#9aa3b8 0%,#3a4052 35%,#0e121b 70%)}
.wish h2{left:637px;top:96px;font-size:46px;width:500px;text-align:left}
.wish h3{left:637px;top:236px;font-size:19px;font-weight:700;line-height:30px;width:460px}
.wish .copy{left:637px;top:314px;width:470px;font-size:13px;line-height:25px}

/* employee */
.employee{top:2336px;height:583px;background:var(--bg)}
.employee h2{top:64px;font-size:46px}
.orb{position:absolute;top:168px;width:290px;height:290px;border-radius:50%;background:radial-gradient(circle at 50% 20%,#3a1a95,#120838 80%);border:2px solid rgba(255,255,255,.35);text-align:center;padding-top:62px}
.orb.mid{background:radial-gradient(circle at 50% 20%,#4d3ef0,#5b1fc0 80%);border:4px solid #fff}
.orb svg{width:50px;height:50px;stroke:#fff;fill:none;stroke-width:1.6}
.orb h4{font-size:15px;font-weight:600;margin-top:20px}
.orb p{font-size:11px;line-height:22px;margin:12px auto 0;width:180px;color:var(--muted)}
.orb .rule{width:34px;height:2px;background:#fff;margin:20px auto 0}
.ring{position:absolute;top:158px;width:310px;height:310px;border-radius:50%;border:2px solid rgba(255,255,255,.6);border-bottom-color:transparent}

/* ready */
.ready{top:2919px;left:110px;width:980px;height:460px;border:3px solid #8b8fa5;border-radius:8px;background:linear-gradient(180deg,#141823,#0a0d16)}
.ready h2{top:56px;left:0;width:974px;text-align:center;font-size:46px}
.ready .kicker{top:190px;left:0;width:974px;text-align:center;color:var(--orange);font-weight:600;font-size:19px}
.ready .lead{top:222px;left:0;width:974px;text-align:center;font-weight:600;font-size:19px}
.ready .copy{top:262px;left:110px;width:754px;text-align:center}
.ready .btn{left:346px;top:364px}

/* faq */
.faq{top:3379px;height:512px}
.faq h2{top:80px;font-size:46px}
.faq-item{position:absolute;left:197px;width:808px;height:72px;border-radius:36px;background:var(--lavender);color:#1b1540;font-size:14px;font-weight:600;display:flex;align-items:center;justify-content:space-between;padding:0 14px 0 30px}
.faq-item .chev{width:52px;height:52px;border-radius:50%;background:#1b1035;display:flex;align-items:center;justify-content:center}
.faq-item .chev svg{width:16px;height:16px;stroke:#fff;fill:none;stroke-width:2.4}

/* reviews */
.reviews{top:3891px;height:640px}
.review-card{left:110px;top:0;width:980px;height:437px;border:3px solid #b9aef0;border-radius:6px;background:linear-gradient(135deg,#3c1cc4 0%,#6a2ae0 55%,#2a1690 100%)}
.review-card h2{font-family:var(--serif);font-weight:400;font-size:41px;line-height:53px;text-align:center;margin-top:56px}
.stars{text-align:center;margin-top:20px;display:flex;justify-content:center;gap:4px}
.stars svg{width:26px;height:26px;fill:var(--orange)}
.robot-visual{left:500px;top:318px;width:200px;height:250px;border-radius:90px 90px 60px 60px;background:radial-gradient(circle at 50% 35%,#f2f3f7 0%,#b9bccb 50%,rgba(60,28,196,0) 75%)}

/* possibilities */
.possible{top:4531px;height:424px}
.possible h2{top:20px;font-size:46px;line-height:56px;background:linear-gradient(90deg,#b7a0f4,#e9c7f2 50%,#f4b27a);-webkit-background-clip:text;background-clip:text;color:transparent}
.possible .copy{top:200px;left:220px;width:760px;text-align:center}
.possible .btn{top:300px}

/* footer */
.site-footer{top:4955px;height:388px;background:#000}
.site-footer .brand{position:absolute;top:60px;left:0;width:1200px}
.site-footer .terms{top:148px;font-size:16px;line-height:28px}
.site-footer .links{top:220px;font-size:11px;font-weight:600;letter-spacing:.3px}
.site-footer .divider{top:262px;left:0;width:1200px;height:1px;background:#2a2d3a}
.site-footer .copyright{top:282px;font-size:11px;font-weight:500}
</style>
</head>
<body>

<section class="hero">
  <div class="brand">Halvora</div>
  <h1 class="abs center serif-title">AI Voice Agents That Can</h1>
  <div class="abs hero-visual" role="img" aria-label="Glowing AI brain on a purple sound-wave backdrop"></div>

  <div class="feature" style="left:294px;top:253px"><div class="ico"><svg viewBox="0 0 24 24"><path d="M5 3h4l2 5-3 2a12 12 0 0 0 6 6l2-3 5 2v4a2 2 0 0 1-2 2A18 18 0 0 1 3 5a2 2 0 0 1 2-2z"/></svg></div>Transfer Calls</div>
  <div class="feature" style="left:758px;top:257px"><div class="ico"><svg viewBox="0 0 24 24"><circle cx="12" cy="12" r="9"/><path d="M9 15l1.5-6h3L15 15M10 13h4"/></svg></div>Answer Calls</div>
  <div class="feature" style="left:58px;top:367px"><div class="ico"><svg viewBox="0 0 24 24"><path d="M6 16V11a6 6 0 0 1 12 0v5l2 2H4z"/><path d="M10 20a2 2 0 0 0 4 0"/></svg></div>Follow Up with Reminders</div>
  <div class="feature" style="left:941px;top:358px"><div class="ico"><svg viewBox="0 0 24 24"><rect x="4" y="5" width="16" height="15" rx="2"/><path d="M4 10h16M9 14h1M14 14h1M9 17h1M14 17h1"/></svg></div>Book Appointments</div>
  <div class="feature" style="left:752px;top:456px"><div class="ico"><svg viewBox="0 0 24 24"><rect x="3" y="6" width="18" height="13" rx="2"/><path d="M3 7l9 6 9-6"/></svg></div>Send Emails</div>
  <div class="feature" style="left:217px;top:504px"><div class="ico"><svg viewBox="0 0 24 24"><path d="M4 5h16v11H9l-5 4z"/><path d="M8 10h8M8 13h5"/></svg></div>Send Text Messages</div>

  <h2 class="abs center">Available 24 Hours, 7 Days a Week!</h2>
  <p class="abs copy">We Will Create An Ai Agent Customized For Your Business At No Cost. Simply Click The Button Above And Your Very Own Ai Agent Will Be Calling You In Just A Couple Minutes. Experience The Magic And Get Ready To Be Very Impressed!</p>
  <a class="btn" style="top:765px">GET AN INSTANT FREE DEMO <svg viewBox="0 0 16 16"><circle cx="8" cy="8" r="8" fill="#fff"/><path d="M7 5l3 3-3 3" stroke="#4a2bd6" stroke-width="2" fill="none"/></svg></a>
</section>

<section class="workforce">
  <h2 class="abs center serif-title">Meet Your New AI-<br>Powered Workforce</h2>

  <div class="agent" style="left:87px;top:260px;width:162px;height:207px"><div class="ph" role="img" aria-label="Small dark robot with glowing blue eyes" style="background:linear-gradient(160deg,#1a2740,#0a1020)"></div></div>
  <div class="agent" style="left:263px;top:235px;width:197px;height:257px"><div class="ph" role="img" aria-label="Cyborg woman with blue circuit details" style="background:linear-gradient(160deg,#2b4f7a,#0c1a30)"></div></div>
  <div class="agent" style="left:479px;top:202px;width:247px;height:321px"><div class="ph" role="img" aria-label="White friendly robot with glowing visor" style="background:linear-gradient(160deg,#c9ccd6,#6d7485)"></div></div>
  <div class="agent" style="left:742px;top:235px;width:197px;height:257px"><div class="ph" role="img" aria-label="Humanoid robot seated at a reception desk" style="background:linear-gradient(160deg,#6b5a48,#2a2420)"></div></div>
  <div class="agent" style="left:960px;top:260px;width:159px;height:207px"><div class="ph" role="img" aria-label="White robot working on a laptop" style="background:linear-gradient(160deg,#e4e5ea,#9a9ca6)"></div></div>

  <div class="agent-label" style="left:48px;top:486px">AI FOLLOW UP REMINDERS</div>
  <div class="agent-label" style="left:241px;top:512px;font-size:13px">AI LEAD QUALIFIER</div>
  <div class="agent-label" style="left:720px;top:505px;font-size:13px">AI RECEPTIONIST</div>
  <div class="agent-label" style="left:920px;top:486px">AI APPOINTMENT SETTER</div>

  <div class="arrow" style="left:59px;top:360px"><svg viewBox="0 0 20 20"><path d="M10 5l-5 5 5 5M15 5l-5 5 5 5"/></svg></div>
  <div class="arrow" style="left:1095px;top:360px"><svg viewBox="0 0 20 20"><path d="M5 5l5 5-5 5M10 5l5 5-5 5"/></svg></div>

  <div class="abs badge"><svg viewBox="0 0 24 24"><circle cx="12" cy="8" r="3"/><path d="M4 19l4-4h6l3-2M14 15l4-2 2 2-6 5H8"/></svg></div>
  <h3 class="abs center">AI SALES AGENT</h3>
  <p class="abs copy agent-copy">Elliot will take your inbound sales calls. Will give all detailed information to the customer, answer questions in a normal conversational tone and can book sales appointments or transfer hot prospects to a human to close the sale.</p>
  <a class="btn" style="top:730px">GET AN INSTANT FREE DEMO <svg viewBox="0 0 16 16"><circle cx="8" cy="8" r="8" fill="#fff"/><path d="M7 5l3 3-3 3" stroke="#4a2bd6" stroke-width="2" fill="none"/></svg></a>
  <p class="abs copy foot-copy">We Will Create An Ai Agent Customized For Your Business At No Cost. Simply Click The Button Above And Your Very Own Ai Agent Will Be Calling You In Just A Couple Minutes. Experience The Magic And Get Ready To Be Very Impressed!</p>
</section>

<section class="wish">
  <div class="abs wish-visual" role="img" aria-label="Glowing digital brain floating above an open hand"></div>
  <h2 class="abs serif-title">Your Wish Is<br>Their Command</h2>
  <h3 class="abs">Your New Ai Agents Will Never Call In Sick<br>And Will Never Complain!</h3>
  <p class="abs copy">With your new team of AI Agents, handling inbound calls, sending emails and sms messages, booking appointments and handling customer service inquiries is going to save you a ton of time and money.</p>
</section>

<section class="employee">
  <h2 class="abs center serif-title">An Employee That Never Gets Sick!</h2>
  <div class="ring" style="left:133px"></div>
  <div class="ring" style="left:757px"></div>
  <div class="orb" style="left:143px"><svg viewBox="0 0 48 48"><path d="M20 30V12a3 3 0 0 1 6 0v12l10 2a4 4 0 0 1 3 5l-2 9H22l-8-10 2-2 4 2"/><path d="M15 14a9 9 0 0 1 16 0"/></svg><h4>TRAINED IN SECONDS</h4><p>Learns Your Entire Website In Seconds</p><div class="rule"></div></div>
  <div class="orb mid" style="left:456px"><svg viewBox="0 0 48 48"><path d="M20 30V16a3 3 0 0 1 6 0v10l9 2a4 4 0 0 1 3 5l-2 9H22l-8-10 2-2 4 2"/><circle cx="23" cy="8" r="3"/><path d="M15 8h-3M34 8h-3M17 3l-2-2M29 3l2-2"/></svg><h4>WORLDWIDE</h4><p>Works Anywhere In The Globe</p><div class="rule"></div></div>
  <div class="orb" style="left:767px"><svg viewBox="0 0 48 48"><path d="M14 42V32a14 14 0 1 1 20-12l4 8h-4v6h-6v8"/><path d="M26 12l-4 7h5l-3 7"/></svg><h4>USER-FRIENDLY</h4><p>Your AI Agents Sound As If They're Real Humans</p><div class="rule"></div></div>
</section>

<section class="ready">
  <h2 class="abs serif-title">Our AI Agents Our Ready<br>To Be Hired</h2>
  <p class="abs kicker">Lightning-Fast Responses</p>
  <p class="abs lead">Instant answers, no coffee, bathroom or lunch breaks needed</p>
  <p class="abs copy">We Will Create An Ai Agent Customized For Your Business At No Cost. Simply Click The Button Above And Your Very Own Ai Agent Will Be Calling You In Just A Couple Minutes. Experience The Magic And Get Ready To Be Very Impressed!</p>
  <a class="btn ghost">GET AN INSTANT FREE DEMO <svg viewBox="0 0 16 16"><circle cx="8" cy="8" r="8" fill="#fff"/><path d="M7 5l3 3-3 3" stroke="#111" stroke-width="2" fill="none"/></svg></a>
</section>

<section class="faq">
  <h2 class="abs center serif-title">Do You Have Questions?</h2>
  <div class="faq-item" style="top:191px">WHAT EXACTLY ARE THE AI VOICE AGENTS?<span class="chev"><svg viewBox="0 0 16 16"><path d="M4 4l4 4 4-4M4 9l4 4 4-4"/></svg></span></div>
  <div class="faq-item" style="top:274px">HOW WILL THESE AI VOICE AGENTS BENEFIT<span class="chev"><svg viewBox="0 0 16 16"><path d="M4 4l4 4 4-4M4 9l4 4 4-4"/></svg></span></div>
  <div class="faq-item" style="top:356px">ARE THEY EASY TO USE?<span class="chev"><svg viewBox="0 0 16 16"><path d="M4 4l4 4 4-4M4 9l4 4 4-4"/></svg></span></div>
</section>

<section class="reviews">
  <div class="abs review-card">
    <h2>After Our Customers Have A<br>Conversation With Their New Ai Voice<br>Agent They Give Us 5 Stars!</h2>
    <div class="stars">
      <svg viewBox="0 0 24 24"><path d="M12 2l3 7 7 .6-5.3 4.7 1.6 7.2L12 17.8 5.7 21.5l1.6-7.2L2 9.6 9 9z"/></svg>
      <svg viewBox="0 0 24 24"><path d="M12 2l3 7 7 .6-5.3 4.7 1.6 7.2L12 17.8 5.7 21.5l1.6-7.2L2 9.6 9 9z"/></svg>
      <svg viewBox="0 0 24 24"><path d="M12 2l3 7 7 .6-5.3 4.7 1.6 7.2L12 17.8 5.7 21.5l1.6-7.2L2 9.6 9 9z"/></svg>
      <svg viewBox="0 0 24 24"><path d="M12 2l3 7 7 .6-5.3 4.7 1.6 7.2L12 17.8 5.7 21.5l1.6-7.2L2 9.6 9 9z"/></svg>
      <svg viewBox="0 0 24 24"><path d="M12 2l3 7 7 .6-5.3 4.7 1.6 7.2L12 17.8 5.7 21.5l1.6-7.2L2 9.6 9 9z"/></svg>
    </div>
  </div>
  <div class="abs robot-visual" role="img" aria-label="Small white robot with glowing blue eyes"></div>
</section>

<section class="possible">
  <h2 class="abs center serif-title">These AI Agents Can Help Your Business<br>Tremendously. Imagine The<br>Possibilities</h2>
  <p class="abs copy">We Will Create An Ai Agent Customized For Your Business At No Cost. Simply Click The Button Above And Your Very Own Ai Agent Will Be Calling You In Just A Couple Minutes. Experience The Magic And Get Ready To Be Very Impressed!</p>
  <a class="btn">GET AN INSTANT FREE DEMO <svg viewBox="0 0 16 16"><circle cx="8" cy="8" r="8" fill="#fff"/><path d="M7 5l3 3-3 3" stroke="#4a2bd6" stroke-width="2" fill="none"/></svg></a>
</section>

<footer class="site-footer">
  <div class="brand">Halvora</div>
  <p class="abs center terms">14-Day Money Back Guarantee Terms: If you use the ai agents and you're not happy.<br>Then you can contact us in the first 14 days for a full refund.</p>
  <p class="abs center links">PRIVACY | TERMS &amp; CONDITIONS | EARNINGS &amp; PRODUCTS DISCLAIMER</p>
  <div class="abs divider"></div>
  <p class="abs center copyright">Copyright@2025.All Rights Reserved</p>
</footer>

</body>
</html>
```